RWT Fittings Ltd Business Cards

We need a business card with our business logo. We provide window and door installations on high-rises in west coast British Colombia, Canada.

I would like my business information and details on one side of the card, and the other side the company name with logo

Target Market(s)

General Contractors

Industry/Entity Type

Construction

Contact Information for Business Card

one side i want my company name and logo in the dark theme logo that i provided

Requirements
Must have
• Marco Peltieri, 16045518293, RWTFittings@mailbox-demo.com, 1407-5194 Linden Row Burnaby BC, V5H 2K9, Owner & Manager

```html
<!DOCTYPE html>
<html lang="en">
<head>
<meta charset="utf-8">
<title>RWT Fittings Ltd – Business Cards</title>
<link rel="stylesheet" href="https://fonts.googleapis.com/css2?family=Open+Sans:wght@400;600;700&display=swap">
<style>
  :root {
    --backdrop: #3a3a3a;
    --card-dark: #161616;
    --card-grey: #9a9a9a;
    --accent-blue: #29a3e0;
    --text-light: #e6e6e6;
    --text-white: #f4f4f4;
    --mark-tone-a: #262626;
    --mark-tone-b: #1b1b1b;
  }
  * { margin: 0; padding: 0; box-sizing: border-box; }
  html, body { width: 1200px; height: 780px; overflow: hidden; }
  body {
    background: var(--backdrop);
    font-family: "Open Sans", Arial, sans-serif;
    position: relative;
  }
  .card {
    position: absolute;
    top: 235px;
    width: 540px;
    height: 310px;
    border-radius: 24px;
    overflow: hidden;
  }
  /* Contact side */
  .card--contact {
    left: 40px;
    background: var(--card-dark);
    color: var(--text-light);
  }
  .brand-mark-area {
    position: absolute;
    right: 0;
    bottom: 0;
    width: 300px;
    height: 240px;
    background: linear-gradient(135deg, var(--mark-tone-b) 0%, var(--mark-tone-a) 55%, var(--mark-tone-b) 100%);
    border-top-left-radius: 40px;
  }
  .contact-wordmark {
    position: absolute;
    left: 34px;
    top: 30px;
    display: flex;
    align-items: center;
    gap: 10px;
  }
  .contact-wordmark__square {
    width: 16px;
    height: 16px;
    background: var(--accent-blue);
  }
  .contact-wordmark__name {
    font-weight: 700;
    font-size: 26px;
    letter-spacing: 1px;
    color: var(--accent-blue);
    text-transform: uppercase;
  }
  .person {
    position: absolute;
    left: 34px;
    top: 92px;
    padding-left: 14px;
    border-left: 8px solid var(--accent-blue);
  }
  .person__name {
    font-weight: 600;
    font-size: 20px;
    color: var(--accent-blue);
    text-transform: uppercase;
    line-height: 1.1;
  }
  .person__title {
    font-size: 13px;
    margin-top: 2px;
  }
  .address {
    position: absolute;
    left: 56px;
    top: 152px;
    font-size: 12.5px;
    line-height: 1.45;
    width: 220px;
  }
  .contact-list {
    position: absolute;
    left: 34px;
    top: 208px;
    list-style: none;
    font-size: 12.5px;
    line-height: 1.65;
  }
  .contact-list li { display: flex; align-items: center; gap: 8px; }
  .contact-list svg { width: 12px; height: 12px; fill: var(--accent-blue); flex: none; }

  /* Brand side */
  .card--brand {
    left: 620px;
    background: var(--card-grey);
    display: flex;
    align-items: center;
    justify-content: center;
    gap: 16px;
  }
  .brand-wordmark__square {
    width: 34px;
    height: 34px;
    background: var(--text-white);
  }
  .brand-wordmark__name {
    font-weight: 700;
    font-size: 40px;
    letter-spacing: 2px;
    color: var(--text-white);
    text-transform: uppercase;
  }
</style>
</head>
<body>
  <section class="card card--contact" aria-label="Contact side">
    <div class="brand-mark-area" role="img" aria-label="Faint tonal decoration area in dark greys"></div>
    <div class="contact-wordmark">
      <span class="contact-wordmark__square"></span>
      <span class="contact-wordmark__name">RWT Fittings Ltd</span>
    </div>
    <div class="person">
      <p class="person__name">Marco Peltieri</p>
      <p class="person__title">Owner &amp; Manager</p>
    </div>
    <p class="address">1407-5194 Linden Row<br>Burnaby BC, V5H 2K9</p>
    <ul class="contact-list">
      <li>
        <svg viewBox="0 0 24 24" aria-hidden="true"><path d="M6.6 10.8a15 15 0 0 0 6.6 6.6l2.2-2.2a1 1 0 0 1 1-.25 11.4 11.4 0 0 0 3.6.6 1 1 0 0 1 1 1V20a1 1 0 0 1-1 1A17 17 0 0 1 3 4a1 1 0 0 1 1-1h3.5a1 1 0 0 1 1 1c0 1.25.2 2.45.6 3.6a1 1 0 0 1-.25 1z"/></svg>
        16045518293
      </li>
      <li>
        <svg viewBox="0 0 24 24" aria-hidden="true"><path d="M2 5h20v14H2zm2 2v.5l8 5 8-5V7l-8 5z"/></svg>
        RWTFittings@mailbox-demo.com
      </li>
      <li>
        <svg viewBox="0 0 24 24" aria-hidden="true"><circle cx="12" cy="12" r="10"/></svg>
        www.rwtfittings-demo.com
      </li>
    </ul>
  </section>

  <section class="card card--brand" aria-label="Brand side">
    <span class="brand-wordmark__square"></span>
    <span class="brand-wordmark__name">RWT Fittings Ltd</span>
  </section>
</body>
</html>
```